KRL Stationery Design Project

Dear Designers,
We need a new stationery design for company to match our new logo.
Designers should provide a design for the following:
1. Business Card: 3.5x2 Inches.
2. Letterhead: A4 size.
3. Envelops: 25x35.5 Cm.
You can keep the Arabic name at the bottom of the logo Or you can use the separate attached Arabic Name.
Please refer to the attached logo guide for design information.
Sample Business Card information:
Name: Tarek Sowan
Position: Operation Manager
Tel: +966 920007164 Ex. 500
Fax: +966 (3)8842617
Mob: +966 (5)00263817
email: tarek@krl-example.com.sa
URL: www.krl-example.com.sa
Address:
Nakheel Heights, Suite 718
Zayed bin Omar Str.
Khobar, 31847
Saudi Arabia
Updates
Dear All,
Please note, we had uploaded our logo along with Arabic writing in Adobe illustrator format (.ai).
Regards,
Karim
Dear All,
A sample data for the business card had been added as per your request.
Regards,
Karim

```html
<!DOCTYPE html>
<html lang="en">
<head>
<meta charset="utf-8">
<title>KRL Business Card</title>
<link href="https://fonts.googleapis.com/css2?family=Source+Sans+3:wght@400;600;700;800&display=swap" rel="stylesheet">
<style>
  :root {
    --navy: #0d2b52;
    --grey-band: #9b9ca1;
    --text-grey: #4a4a4a;
    --pale: #cdd3dc;
    --card: #ffffff;
    --backdrop: #2e2e2e;
  }
  * { margin: 0; padding: 0; box-sizing: border-box; }
  html, body { width: 1200px; height: 472px; overflow: hidden; }
  body {
    background: var(--backdrop);
    font-family: "Source Sans 3", sans-serif;
    position: relative;
  }
  .card {
    position: absolute;
    top: 84px;
    width: 525px;
    height: 299px;
    background: var(--card);
    box-shadow: 0 2px 6px rgba(0,0,0,.45);
    overflow: hidden;
  }
  .card--front { left: 58px; }
  .card--back { left: 603px; }

  .edge-band { position: absolute; left: 0; width: 9px; }
  .edge-band--top { top: 0; height: 152px; background: var(--navy); }
  .edge-band--bottom { top: 152px; height: 147px; background: var(--grey-band); }

  .brand-name {
    position: absolute;
    color: var(--navy);
    font-weight: 800;
    line-height: 1;
    letter-spacing: 1px;
  }
  .card--front .brand-name { left: 42px; top: 70px; font-size: 52px; }
  .card--back .brand-name { left: 0; width: 100%; text-align: center; top: 82px; font-size: 64px; }

  .decor { position: absolute; background: var(--pale); opacity: .8; }
  .decor--satellite { left: 350px; top: 28px; width: 120px; height: 60px; border-radius: 4px; }
  .decor--vehicle { left: 382px; top: 248px; width: 143px; height: 51px; clip-path: polygon(0 100%, 100% 20%, 100% 100%); }

  .holder { position: absolute; right: 28px; top: 108px; text-align: right; }
  .holder__name { font-size: 18px; font-weight: 700; color: var(--navy); line-height: 1.1; }
  .holder__title { font-size: 13px; color: var(--text-grey); margin-top: 4px; }

  .contact-list { position: absolute; right: 27px; top: 168px; list-style: none; }
  .contact-list li {
    display: flex; align-items: center; justify-content: flex-end; gap: 6px;
    font-size: 13.5px; color: var(--text-grey); letter-spacing: .6px; height: 16.7px;
  }
  .contact-list svg { width: 10px; height: 10px; fill: var(--navy); }

  .address {
    position: absolute; left: 31px; top: 268px;
    font-size: 13.5px; color: var(--text-grey); letter-spacing: 1px;
  }

  .web {
    position: absolute; left: 0; width: 100%; top: 242px; text-align: center;
    font-size: 13.5px; color: var(--text-grey); letter-spacing: 2.2px;
  }
</style>
</head>
<body>
  <section class="card card--front">
    <div class="edge-band edge-band--top"></div>
    <div class="edge-band edge-band--bottom"></div>

    <div class="brand-name">KRL</div>

    <div class="decor decor--satellite" role="img" aria-label="Faint satellite illustration"></div>
    <div class="decor decor--vehicle" role="img" aria-label="Faint truck illustration"></div>

    <div class="holder">
      <div class="holder__name">Your Name</div>
      <div class="holder__title">Title</div>
    </div>

    <ul class="contact-list">
      <li>123-456-7890
        <svg viewBox="0 0 10 10"><path d="M2 0.5l2 2-1 1.2c.6 1.3 1.5 2.2 2.8 2.8l1.2-1 2 2-1.2 1.8C4.5 9 1 5.5.5 1.7z"/></svg>
      </li>
      <li>123-456-7890
        <svg viewBox="0 0 10 10"><rect x="2.5" y="0.5" width="5" height="9" rx="1"/><rect x="3.3" y="1.5" width="3.4" height="5.8" fill="#fff"/></svg>
      </li>
      <li>info@mailbox-example.com
        <svg viewBox="0 0 10 10"><rect x="0.5" y="2" width="9" height="6.5" rx=".6"/><path d="M1 2.6l4 3 4-3" stroke="#fff" stroke-width=".9" fill="none"/></svg>
      </li>
      <li>www.website.com
        <svg viewBox="0 0 10 10"><circle cx="5" cy="5" r="4.6"/><path d="M.6 5h8.8M5 .5c-2 2.5-2 6.5 0 9M5 .5c2 2.5 2 6.5 0 9" stroke="#fff" stroke-width=".7" fill="none"/></svg>
      </li>
    </ul>

    <div class="address">Street Name, City Name State, City Zip Code</div>
  </section>

  <section class="card card--back">
    <div class="brand-name">KRL</div>
    <div class="web">www.website.com</div>
  </section>
</body>
</html>
```